New Business card design to reflect rebrand

I would like a business card design with a good base colour for our new logo and also a placeholder for a profile pic of the card holder. the design needs to be editable to the point that we can easily change the picture of the person and use that design for printmerlo etc. we are looking at a metalic finish business card so will need a good base colour to bring out the finish.

Target Market(s)

prospective customers

Industry/Entity Type

Business

Contact Information for Business Card

I would like one editable design that we can change the name of the card holder and profile picture. The design need to be in a format that be send to printmerlo etc.

Our address is Fenwick Lodge, Copse Lane, Ashcombe Vale, GU14 3TP Tel no. 01483 556172

Requirements
Must have
• place holder for a profile pic for the card holder. in AI or preferably PSD format

```html
<!DOCTYPE html>
<html lang="en">
<head>
<meta charset="utf-8">
<title>Corvane Workplace Services – Business Card</title>
<link href="https://fonts.googleapis.com/css2?family=Questrial&family=Open+Sans:wght@400&display=swap" rel="stylesheet">
<style>
  :root {
    --orange: #ec6400;
    --navy: #3d5370;
    --card-light: #f4f2f1;
    --card-shade: #e6e2e0;
    --text-dark: #2f2f33;
    --white: #ffffff;
    --page: #dcdcdc;
  }
  html, body {
    margin: 0;
    width: 1200px;
    height: 900px;
    overflow: hidden;
    background: var(--page);
  }
  .card {
    position: absolute;
    left: 100px;
    top: 140px;
    width: 1000px;
    height: 620px;
    overflow: hidden;
    background: linear-gradient(180deg, var(--card-light) 0%, var(--card-shade) 100%);
    box-shadow: 0 8px 30px rgba(0,0,0,0.18);
  }
  .name-band {
    position: absolute;
    left: 0; top: 0;
    width: 100%; height: 121px;
    background: var(--orange);
    display: flex;
    align-items: center;
    justify-content: center;
  }
  .holder-name {
    margin: 0;
    font-family: "Questrial", sans-serif;
    font-weight: 400;
    font-size: 36px;
    letter-spacing: 2px;
    color: var(--white);
    text-transform: uppercase;
  }
  .profile-photo {
    position: absolute;
    left: 0; top: 121px;
    width: 290px; height: 353px;
    background: linear-gradient(180deg, #bfc3c8 0%, #7b8190 45%, #1f2538 100%);
  }
  .brand {
    position: absolute;
    left: 358px; top: 168px;
    width: 540px;
    display: flex;
    flex-direction: column;
    align-items: center;
  }
  .brand-mark {
    width: 44px; height: 44px;
    background: var(--navy);
    margin-bottom: 52px;
  }
  .brand-name {
    margin: 0;
    font-family: "Questrial", sans-serif;
    font-weight: 400;
    color: var(--navy);
    text-transform: uppercase;
    text-align: center;
  }
  .brand-name .primary {
    display: block;
    font-size: 70px;
    line-height: 1;
    letter-spacing: 4px;
  }
  .brand-name .secondary {
    display: block;
    margin-top: 8px;
    font-size: 33px;
    line-height: 1.1;
    letter-spacing: 4px;
  }
  .contact {
    position: absolute;
    right: 30px; top: 420px;
    font-family: "Open Sans", sans-serif;
    font-size: 23px;
    color: var(--text-dark);
    text-align: right;
  }
  .contact-line {
    display: flex;
    align-items: center;
    justify-content: flex-end;
    gap: 10px;
    height: 36px;
  }
  .contact-line svg { width: 16px; height: 16px; }
  .footer-shape {
    position: absolute;
    left: 0; top: 0;
    width: 1000px; height: 620px;
  }
  .address {
    position: absolute;
    left: 59px; top: 510px;
    margin: 0;
    font-family: "Open Sans", sans-serif;
    font-style: normal;
    font-size: 24px;
    line-height: 37px;
    color: var(--white);
  }
</style>
</head>
<body>
  <section class="card">
    <svg class="footer-shape" viewBox="0 0 1000 620" aria-hidden="true">
      <polygon points="286,457 320,457 1000,606 1000,620 960,620 290,474" fill="var(--navy)"/>
      <polygon points="0,474 290,474 960,620 0,620" fill="var(--orange)"/>
    </svg>

    <header class="name-band">
      <h1 class="holder-name">Daniel Hartwell</h1>
    </header>

    <div class="profile-photo" role="img" aria-label="Profile photo of the card holder"></div>

    <div class="brand">
      <span class="brand-mark"></span>
      <p class="brand-name"><span class="primary">Corvane</span><span class="secondary">Workplace Services</span></p>
    </div>

    <div class="contact">
      <div class="contact-line">
        <span>01483 556172</span>
        <svg viewBox="0 0 16 16" aria-hidden="true"><path d="M3 2h3l1.5 3.5-2 1.2a8 8 0 0 0 3.8 3.8l1.2-2L14 10v3a1 1 0 0 1-1 1A11 11 0 0 1 2 3a1 1 0 0 1 1-1z" fill="var(--orange)"/></svg>
      </div>
      <div class="contact-line">
        <span>info@corvane.com</span>
        <svg viewBox="0 0 16 16" aria-hidden="true"><rect x="1" y="3" width="14" height="10" fill="var(--orange)"/><path d="M1 3l7 6 7-6" fill="none" stroke="var(--white)" stroke-width="1.3"/></svg>
      </div>
    </div>

    <address class="address">Fenwick Lodge, Copse Lane,<br>Ashcombe Vale, GU14 3TP</address>
  </section>
</body>
</html>
```